Halvorsen Ridge Consulting Needs a Letterhead

Tomi, we need a letterhead/banner for our blog, which is titled "Marigold Crossroads". The letterhead/banner should incorporate the enclosed banner image, logo, and the name of our blog ("Marigold Crossroads").

We would also like an alternative design that includes our picture. Here, we have two options that we would like to see.

In all, we would like to see 3 different designs: one banner without any pics; and two banner with two versions of our pictures.

The file size should be able to be resized for the space given to us at our website (http://halvorsen-ridge-consulting.com).

We also need the letterhead/banner by Friday, June 13. Thanks!!

```html
<!DOCTYPE html>
<html lang="en">
<head>
<meta charset="utf-8">
<title>Marigold Crossroads — Blog Banner</title>
<link rel="stylesheet" href="https://fonts.googleapis.com/css2?family=Kalam:wght@300&display=swap">
<style>
  :root {
    --banner-bg: #000000;
    --gold: #c9b97a;
  }
  html, body {
    margin: 0;
    padding: 0;
    width: 1200px;
    height: 250px;
    overflow: hidden;
    background: var(--banner-bg);
  }
  .banner {
    position: relative;
    width: 1200px;
    height: 250px;
    background: var(--banner-bg);
    overflow: hidden;
  }
  .blog-title {
    margin: 0;
    font-family: "Kalam", cursive;
    font-weight: 300;
    color: var(--gold);
    line-height: 1;
  }
  .blog-title__line {
    position: absolute;
    display: block;
    font-size: 70px;
    letter-spacing: 0.5px;
    white-space: nowrap;
  }
  .blog-title__line--first {
    left: 12px;
    top: 22px;
  }
  .blog-title__line--second {
    left: 250px;
    top: 128px;
  }
  .company-mark {
    position: absolute;
    left: 900px;
    top: 88px;
    width: 270px;
    display: flex;
    align-items: center;
    gap: 14px;
    font-family: "Kalam", cursive;
    font-weight: 300;
    color: var(--gold);
  }
  .company-mark__square {
    flex: 0 0 auto;
    width: 22px;
    height: 22px;
    background: var(--gold);
  }
  .company-mark__name {
    font-size: 28px;
    line-height: 1.1;
  }
</style>
</head>
<body>
  <header class="banner">
    <h1 class="blog-title">
      <span class="blog-title__line blog-title__line--first">Marigold</span>
      <span class="blog-title__line blog-title__line--second">Crossroads</span>
    </h1>
    <div class="company-mark">
      <span class="company-mark__square" aria-hidden="true"></span>
      <span class="company-mark__name">Halvorsen Ridge Consulting</span>
    </div>
  </header>
</body>
</html>
```